Business Cards for a law firm

Business cards for our law firm. Use our silhoette logo and OAK PARTNERS - check our website (www.oakpartners.example)

Contact Information for Business Card

our silhouette logo, OAK PARTNERS, 800-555-0147, Dorian Pemberton, dorian@oakpartners.example

Requirements
Must have
• our silhouette logo, OAK PARTNERS, 800-555-0147, Dorian Pemberton, dorian@oakpartners.example

```html
<!DOCTYPE html>
<html lang="en">
<head>
<meta charset="utf-8">
<title>Oak Partners — Business Cards</title>
<link href="https://fonts.googleapis.com/css2?family=Cinzel:wght@600&family=Arimo:wght@400&display=swap" rel="stylesheet">
<style>
  :root {
    --backdrop: #2e2e2e;
    --navy: #1b316b;
    --white: #ffffff;
    --card-shadow: rgba(0, 0, 0, 0.45);
  }
  * { margin: 0; padding: 0; box-sizing: border-box; }
  html, body {
    width: 1200px;
    height: 689px;
    overflow: hidden;
    background: var(--backdrop);
  }
  .stage {
    position: relative;
    width: 1200px;
    height: 689px;
  }
  .card {
    position: absolute;
    top: 201px;
    width: 500px;
    height: 286px;
    border-radius: 18px;
    overflow: hidden;
    box-shadow: 0 12px 30px var(--card-shadow);
  }
  /* Back of card */
  .card-back {
    left: 60px;
    background: var(--navy);
    color: var(--white);
  }
  .card-back .brand-name {
    position: absolute;
    left: 0; right: 0;
    top: 110px;
    text-align: center;
    font-family: "Cinzel", serif;
    font-weight: 600;
    font-size: 30px;
    letter-spacing: 3px;
  }
  .card-back .website {
    position: absolute;
    left: 0; right: 0;
    bottom: 44px;
    text-align: center;
    font-family: "Arimo", sans-serif;
    font-size: 13px;
  }
  /* Front of card */
  .card-front {
    left: 640px;
    display: flex;
  }
  .brand-panel {
    width: 56%;
    background: var(--white);
    display: flex;
    align-items: center;
    justify-content: center;
    gap: 10px;
    color: var(--navy);
  }
  .brand-panel .brand-mark {
    width: 18px;
    height: 18px;
    background: var(--navy);
  }
  .brand-panel .brand-name {
    font-family: "Cinzel", serif;
    font-weight: 600;
    font-size: 22px;
    letter-spacing: 2px;
  }
  .contact-panel {
    width: 44%;
    background: var(--navy);
    color: var(--white);
    padding: 80px 0 0 22px;
    border-left: 3px solid #111;
  }
  .contact-panel .person-name {
    font-family: "Cinzel", serif;
    font-weight: 600;
    font-size: 17px;
    letter-spacing: 1px;
    margin-bottom: 34px;
  }
  .contact-list { list-style: none; }
  .contact-list li {
    display: flex;
    align-items: center;
    gap: 7px;
    font-family: "Arimo", sans-serif;
    font-size: 10.5px;
    line-height: 17px;
  }
  .contact-list svg { width: 9px; height: 9px; flex: none; fill: var(--white); }
</style>
</head>
<body>
<main class="stage">
  <section class="card card-back" aria-label="Card back">
    <div class="brand-name">OAK PARTNERS</div>
    <div class="website">www.oakpartners.example</div>
  </section>

  <section class="card card-front" aria-label="Card front">
    <div class="brand-panel">
      <span class="brand-mark"></span>
      <span class="brand-name">OAK PARTNERS</span>
    </div>
    <div class="contact-panel">
      <div class="person-name">Dorian Pemberton</div>
      <ul class="contact-list">
        <li>
          <svg viewBox="0 0 10 10" aria-hidden="true"><path d="M2 0.5 L3.6 2.6 L2.7 3.6 Q3.6 5.8 6.4 7.3 L7.4 6.4 L9.5 8 L8.3 9.5 Q2.5 8.5 0.5 1.7 Z"/></svg>
          800-555-0147
        </li>
        <li>
          <svg viewBox="0 0 10 10" aria-hidden="true"><path d="M0.5 2 H9.5 V8 H0.5 Z M1.2 2.6 L5 5.4 L8.8 2.6" stroke="#1b316b" stroke-width="0.8"/></svg>
          dorian@oakpartners.example
        </li>
        <li>
          <svg viewBox="0 0 10 10" aria-hidden="true"><circle cx="5" cy="5" r="4.5"/><path d="M0.5 5 H9.5 M5 0.5 Q2 5 5 9.5 Q8 5 5 0.5" stroke="#1b316b" stroke-width="0.7" fill="none"/></svg>
          www.oakpartners.example
        </li>
      </ul>
    </div>
  </section>
</main>
</body>
</html>
```